Pharmacy ad

need 2 pharmacy ads for the phone book. one for Brookvale Pharmacy and one for Cedarline Care Pharmacy. Dimensions for ad is 4.75in x 4.667 in. please see attached examples of ad uploaded as well logos of each pharmacy

```html
<!DOCTYPE html>
<html lang="en">
<head>
<meta charset="utf-8">
<title>Brookvale Pharmacy – Directory Ad</title>
<link href="https://fonts.googleapis.com/css2?family=Montserrat:wght@400;500;600;700;800&family=Titillium+Web:ital,wght@1,600&display=swap" rel="stylesheet">
<style>
  :root{
    --navy:#1d1b3f;
    --green:#7cbb43;
    --green-deep:#5d9e3a;
    --sky-deep:#5fb3d3;
    --mint:#cde69f;
    --white:#ffffff;
    --social:#3b5a9a;
  }
  *{box-sizing:border-box;margin:0;padding:0}
  html,body{width:1200px;height:1180px;overflow:hidden;background:var(--white)}
  .ad{position:relative;width:1200px;height:1180px;overflow:hidden;font-family:"Montserrat",sans-serif;color:var(--navy);border:4px solid var(--navy)}
  .backdrop{position:absolute;inset:0}

  .offer-line{position:absolute;left:30px;width:520px;text-align:center;line-height:1;white-space:nowrap}
  .offer-pct{font-size:96px;font-weight:800;letter-spacing:-4px}
  .offer-light{font-size:30px;font-weight:400}
  .offer-bold{font-size:28px;font-weight:800}
  .dots{position:absolute;left:44px;height:8px;background:radial-gradient(circle,var(--navy) 3px,transparent 3.5px) 0 0/22.6px 8px repeat-x}

  .brand-mark{position:absolute;left:812px;top:80px;width:190px;height:190px;border-radius:50%;background:var(--green)}
  .brand-name{position:absolute;left:640px;width:540px;top:337px;text-align:center;font-weight:800;font-size:74px;line-height:89px;color:var(--navy);letter-spacing:1px}
  .tagline{position:absolute;left:640px;width:540px;top:530px;text-align:center;font-family:"Titillium Web",sans-serif;font-style:italic;font-weight:600;font-size:32px;color:var(--green-deep)}

  .services{position:absolute;font-size:24.5px;font-weight:700;line-height:28px}
  .services li{list-style:none;position:relative;padding-left:22px}
  .services li::before{content:"";position:absolute;left:2px;top:10px;width:9px;height:9px;background:var(--navy);transform:rotate(45deg)}

  .pay{position:absolute;background:var(--white);display:flex;align-items:center;justify-content:center;font-weight:700;font-size:15px;color:var(--navy);text-align:center;line-height:1.1}

  .inquiry{position:absolute;left:57px;top:905px;font-size:28px;font-weight:500}
  .branch{position:absolute;top:968px}
  .branch .addr{font-size:25px;font-weight:700;line-height:1;display:flex;gap:12px}
  .branch .addr small{display:block;font-size:20px;font-weight:400;margin-top:2px}
  .branch .phone{font-size:25px;font-weight:700;display:flex;align-items:center;gap:10px;margin-top:12px}
  .branch .hours{font-size:26px;font-weight:800;line-height:1.18;margin-top:18px}
  .divider{position:absolute;left:537px;top:957px;width:2px;height:183px;background:var(--navy)}
  .social{position:absolute;left:990px;top:975px;width:150px;text-align:center}
  .social p{font-size:24px;font-weight:500}
  .social .dot{width:80px;height:80px;border-radius:50%;background:var(--social);margin:14px auto 6px}
  .social .name{font-size:17px;font-weight:700}
</style>
</head>
<body>
<main class="ad">
  <svg class="backdrop" width="1200" height="1180" viewBox="0 0 1200 1180" role="img" aria-label="Soft blurred pharmacy shelf backdrop in light blue tones">
    <defs>
      <linearGradient id="sky" x1="0" y1="0" x2="1" y2="1">
        <stop offset="0" stop-color="#a8d8ea"/><stop offset="0.6" stop-color="#7fc3de"/><stop offset="1" stop-color="#9fd3e6"/>
      </linearGradient>
      <radialGradient id="glow" cx="0.45" cy="0.45" r="0.6">
        <stop offset="0" stop-color="#ffffff"/><stop offset="0.7" stop-color="#f1f8fb"/><stop offset="1" stop-color="#d8ecf4"/>
      </radialGradient>
      <linearGradient id="meadow" x1="0" y1="0" x2="1" y2="1">
        <stop offset="0" stop-color="#a6d265"/><stop offset="1" stop-color="#d6ebaf"/>
      </linearGradient>
    </defs>
    <rect width="1200" height="1180" fill="url(#sky)"/>
    <path d="M1200 628 L672 628 L620 592 L0 592 L0 1180 L1200 1180 Z" fill="url(#meadow)"/>
    <path d="M672 628 L1200 628 L1200 965 Q1000 950 860 815 Z" fill="var(--sky-deep)" opacity="0.75"/>
    <circle cx="1060" cy="420" r="490" fill="url(#glow)"/>
    <path d="M840 815 Q990 945 1200 962 L1200 815 Z" fill="#8fcbe1" opacity="0.85"/>
  </svg>

  <section class="offer-block" aria-label="Senior citizen discount">
    <div class="offer-line offer-pct" style="top:28px">10%</div>
    <div class="offer-line offer-light" style="top:120px">SENIOR CITIZEN</div>
    <div class="offer-line offer-light" style="top:155px">DISCOUNT</div>
    <div class="offer-line offer-bold" style="top:188px">FOR PATIENTS</div>
    <div class="offer-line offer-bold" style="top:216px">60 YEARS AND OVER</div>
  </section>
  <div class="dots" style="top:250px;width:492px"></div>
  <section class="offer-block" aria-label="Student discount">
    <div class="offer-line offer-pct" style="top:260px">10%</div>
    <div class="offer-line offer-light" style="top:352px">STUDENT DISCOUNT</div>
    <div class="offer-line offer-bold" style="top:383px">WITH VALID ID CARD</div>
  </section>
  <div class="dots" style="top:417px;width:492px"></div>
  <section class="offer-block" aria-label="Hospital prescription discount">
    <div class="offer-line offer-pct" style="top:424px">10%</div>
    <div class="offer-line offer-light" style="top:518px">DISCOUNT ON HOSPITAL</div>
    <div class="offer-line offer-bold" style="top:548px">PRESCRIPTIONS</div>
  </section>

  <div class="brand-mark"></div>
  <h1 class="brand-name">BROOKVALE<br>PHARMACY</h1>
  <p class="tagline">We Care About Your Health</p>

  <ul class="services" style="left:57px;top:628px">
    <li>Certified Pharmacists</li>
    <li style="margin-top:16px">Affordable prices</li>
    <li style="margin-top:17px">Brand and Generic<br>Medicines</li>
    <li style="margin-top:15px">Blood Pressure and<br>Glucose checks</li>
  </ul>
  <ul class="services" style="left:364px;top:628px">
    <li>Personal care and<br>Beauty Products</li>
    <li style="margin-top:26px">Injectables</li>
    <li style="margin-top:23px">Special Orders</li>
    <li style="margin-top:25px">Delivery service</li>
  </ul>

  <div class="pay" style="left:783px;top:655px;width:105px;height:65px">Paycard</div>
  <div class="pay" style="left:918px;top:655px;width:106px;height:65px">Globex Card</div>
  <div class="pay" style="left:1052px;top:655px;width:92px;height:65px">Harborline</div>
  <div class="pay" style="left:845px;top:738px;width:245px;height:51px;font-size:18px">Keystone Insurance</div>

  <div class="dots" style="top:876px;width:786px"></div>
  <p class="inquiry">For more inquiries, email us: brookvalepharmacy@mailbox.com</p>

  <div class="branch" style="left:57px">
    <div class="addr">
      <svg width="22" height="30" viewBox="0 0 22 30"><path d="M11 0C5 0 0 5 0 11c0 8 11 19 11 19s11-11 11-19C22 5 17 0 11 0z" fill="var(--navy)"/><circle cx="11" cy="11" r="4" fill="var(--mint)"/></svg>
      <div>24 Market Street, Eastport<small>(opposite Grace Chapel)</small></div>
    </div>
    <div class="phone"><svg width="28" height="20" viewBox="0 0 28 20"><path d="M2 6c0-4 24-4 24 0v3h-6V6H8v3H2z M6 10h16l3 10H3z" fill="var(--navy)"/><circle cx="14" cy="15" r="3" fill="var(--mint)"/></svg>1 555 210 4471</div>
    <div class="hours">MONDAY – FRIDAY 10AM TO 6PM<br>SATURDAY 10AM TO 5PM</div>
  </div>
  <div class="divider"></div>
  <div class="branch" style="left:563px">
    <div class="addr">
      <svg width="22" height="30" viewBox="0 0 22 30"><path d="M11 0C5 0 0 5 0 11c0 8 11 19 11 19s11-11 11-19C22 5 17 0 11 0z" fill="var(--navy)"/><circle cx="11" cy="11" r="4" fill="var(--mint)"/></svg>
      <div>Marina Walk, Food Court,<br>Eastport</div>
    </div>
    <div class="phone"><svg width="28" height="20" viewBox="0 0 28 20"><path d="M2 6c0-4 24-4 24 0v3h-6V6H8v3H2z M6 10h16l3 10H3z" fill="var(--navy)"/><circle cx="14" cy="15" r="3" fill="var(--mint)"/></svg>1 555 210 4478</div>
    <div class="hours">MONDAY – SATURDAY<br>9AM TO 5PM</div>
  </div>

  <div class="social">
    <p>Visit us on</p>
    <div class="dot"></div>
    <div class="name">Friendsbook</div>
  </div>
</main>
</body>
</html>
```